Wordpress Theme for Medical Clinics

** Please view updated Sitemap2.pdf doc to clarify some confusion ***

This is a multiuser WordPress subscription site for medical clinics. Please see attachment for sitemap. Please do not include extra content like social media icons, search bars, or images. If you have questions, please ask for clarification.
The site contains the following pages and sub-pages:

1. Home
2. Our Clinic
2a. Our Clinic > Mission
2b. Our Clinic > Services
2c. Our Clinic > Clinic Policies
2d. Our Clinic > Schedules
3. Our Staff
3a. Our Staff > [Staff member page]
4. Resources
4a. Resources > Patient Health (index)
4b. Resources > Patient Health (index) > [post]
4c. Resources > Links
4d. Resources > Forms
5. Alerts
5a. Alerts > [Alert Page]
6. Contact Us

Includes the Following Pages, Subpages, and Content
1. Home
a. About Us
b. Our Staff
c. Bulletins
d. Accepting New Patients (shown as an alert widget)
e. Links
i. Physician Toolbox
ii. Book an Appointment
f. Clinic Policies
i. Show first 3 policies (e.g. Late Arrivals, Missed Appointments, Fees)
ii. Link to Clinic Policies page
g. Primary widget (displayed on all pages)
i. Hours of operation
ii. Contact Info
1. Tel
2. Fax
3. Email
4. Address
5. Get directions (link to Atlas Maps)
2. Our Clinic
a. Main Page
i. Harbourside Clinic
ii. Overview
iii. Languages Spoken
iv. Secondary Navigation
1. Mission
2. Services
3. Clinic Policies
4. Schedules (see attachment)
b. Our Clinic > Mission
c. Our Clinic > Services
i. For each service include service TITLE and DESCRIPTION
d. Our Clinic > Clinic Policies
i. For each policy include policy TITLE and DESCRIPTION
ii. Include the following policies in mockup
1. Late arrivals
2. Missed appointments
3. Fees for missed appointments
4. Referrals and follow-ups
5. Services not covered by RDA
6. Information for LTF patients
7. Medical Legal Reports
e. Our Clinic > Schedules
3. Our Staff
a. Main Page
i. Display a list of staff members. Include NAME and DESIGNATION
b. Our Staff > [Staff Name]
i. Include NAME, PICTURE, DESIGNATION, and BIO
4. Resources
a. Resources > Patient Health
i. Main Page
1. Posts (ordered by date)
a. Title
b. Summary
2. Side Navigation
a. Post Categories
ii. Patient Health > [post title]
1. Title
2. Post Category
3. Date
4. Author
5. Summary
6. Body
b. Resources > Links
1. Secondary Navigation - Categories
a. Sample Categories:
i. Local Services
ii. RDA and Drug Coverage
iii. Mental Health Resources
2. Category page
a. Include the following links in the 'Local Services' category
i. Hypertension clinics
ii. Home Care services
iii. Vaccine Clinics
c. Resources > Forms
i. Display a table with form TITLE and CATEGORY
ii. Side Navigation
1. Form Categories
a. Use the following sample Categories
i. Referrals
ii. Insurance
iii. Intake
iv. Discharge
v. Waivers
5. Alerts
a. Main page
i. List of all Alert posts
1. Include post TITLE as a link to the post
ii. Side Navigation
1. Alerts Archive
a. shown as Month + Number of posts
iii. Alerts > [Alert page]
1. Include TITLE, DATE, AUTHOR, BODY
6. Contact Us
a. Map
b. Hours of operation
c. Address
d. Phone number
e. Fax number
e. Fax number
f. Map
g. Email

Design notes:
- fixed width
- responsive (need designs for mobile, tablet, and desktop)
- simple, dark font, white background
- use Font Awesome icons where needed
- user adds own logo

Target Market(s)

Medical Clinics

Industry/Entity Type

Medical

Number of Pages Required

5+ page

Font styles to use
Serif
Sans Serif

Requirements
Must have
• Please keep designs very simple.
• Examples:
• https://www.quolbin.com/install
• http://www.ventrohax.com/company/about-us
• http://brindlequota.org/
• http://www.trosk.com/
Should not have
• Minimal or no use of shadows and gradients

```html
<!DOCTYPE html>
<html lang="en">
<head>
<meta charset="utf-8">
<title>Harbourside Clinic – Home</title>
<link href="https://fonts.googleapis.com/css2?family=Oswald:wght@400;500&family=Open+Sans:wght@400;600;700&display=swap" rel="stylesheet">
<style>
:root{
  --orange:#f7931e;
  --blue:#2fa3d6;
  --ink:#222;
  --text:#555;
  --muted:#777;
  --panel:#f3f3f3;
  --rule:#e8e8e8;
  --dark:#2b2b2b;
}
*{margin:0;padding:0;box-sizing:border-box}
html,body{width:667px;height:1200px;overflow:hidden;background:#fff}
body{position:relative;font-family:"Open Sans",Arial,sans-serif;color:var(--text)}
a{text-decoration:none;color:inherit}

.site-header{position:absolute;left:0;top:0;width:667px;height:63px;background:var(--panel)}
.brand{position:absolute;left:57px;top:19px;font:600 19px/24px "Open Sans",sans-serif;color:var(--blue)}
.quick-link{position:absolute;top:20px;display:flex;align-items:center;gap:8px;font-family:"Oswald",sans-serif;line-height:1}
.quick-link small{display:block;font-size:9px;color:var(--ink)}
.quick-link strong{display:block;font-weight:400;font-size:14px;margin-top:1px}
.ql-book{left:394px}.ql-book strong{color:var(--orange)}
.ql-tools{left:517px}.ql-tools strong{color:var(--blue)}
.header-divider{position:absolute;left:501px;top:8px;width:1px;height:46px;background:#ddd}

.main-nav{position:absolute;left:53px;top:73px;list-style:none}
.main-nav li{display:flex;align-items:center;height:31px;font:400 11px "Oswald",sans-serif;color:var(--ink)}
.main-nav .dot{width:21px;height:21px;border-radius:50%;background:var(--dark);margin-right:8px;display:flex;align-items:center;justify-content:center}
.main-nav .active{color:var(--orange)}
.main-nav .active .dot{background:var(--orange)}

.content-edge{position:absolute;left:175px;top:63px;width:1px;height:1080px;background:#eee}
.content{position:absolute;left:191px;width:285px}
.section-title{display:flex;align-items:center;gap:8px;font:400 17px/20px "Oswald",sans-serif;color:var(--ink)}
.divider{position:absolute;left:191px;width:285px;height:1px;background:var(--rule)}
.lead{font-size:9px;margin-top:7px}
.btn-solid{display:inline-block;background:var(--orange);color:#fff;font:400 11px/20px "Oswald",sans-serif;padding:0 7px;margin-top:6px;border-radius:2px}
.btn-outline{display:inline-block;border:1px solid var(--orange);color:var(--orange);font:600 7px/15px "Open Sans",sans-serif;padding:0 5px;border-radius:2px}
.body-copy{font-size:8.6px;line-height:16.3px;margin-top:6px;letter-spacing:-.05px}

.staff-list{margin-top:10px;list-style:none}
.staff-row{display:flex;height:49px;margin-bottom:2.3px}
.staff-id{width:100px;background:var(--blue);color:#fff;padding:7px 10px;font-size:7px;position:relative}
.staff-id b{display:block;font-weight:700;margin-bottom:4px}
.staff-id:after{content:"";position:absolute;right:-4px;top:21px;border:4px solid transparent;border-left-color:var(--blue);border-right:0}
.staff-bio{flex:1;background:var(--panel);padding:6px 12px 6px 10px;font-size:6.8px;line-height:11.6px}
.staff-bio i{color:#333}

.alert-item{width:272px}
.alert-item h3{font:700 6.8px/11.5px "Open Sans",sans-serif;color:var(--ink);width:255px}
.alert-item p{font-size:6.8px;line-height:11.5px;margin-top:5px}

.policy-list{list-style:none;margin-top:7px}
.policy-list li{font:400 8px/15.5px "Open Sans",sans-serif;color:var(--ink);display:flex;align-items:center;gap:6px}

.sidebar{position:absolute;left:491px;top:63px;width:135px;height:1080px;background:var(--panel)}
.widget-head{height:39px;display:flex;align-items:center;gap:8px;padding-left:10px;color:#fff;font:400 11px/10px "Oswald",sans-serif}
.widget-head span{font-size:14px;display:block}
.wh-hours{background:var(--blue)}
.wh-contact{background:var(--orange)}
.info-table{font-size:7px;color:var(--ink);padding:0 10px}
.info-row{display:flex;align-items:flex-start}
.info-row dt{width:48px;font-weight:600;font-size:6.5px}
.info-row .sep{width:10px}
.info-row dd{flex:1;line-height:10.5px;color:var(--text)}
.info-row dd.link{color:var(--blue)}

.footer-rule{position:absolute;left:191px;top:1143px;width:435px;height:1px;background:var(--rule)}
.site-footer{position:absolute;left:191px;top:1153px;font-size:7px;line-height:11px;color:var(--ink)}
</style>
</head>
<body>

<header class="site-header">
  <a class="brand" href="#">Harbourside Clinic</a>
  <a class="quick-link ql-book" href="#">
    <svg width="19" height="19" viewBox="0 0 19 19"><rect x="1" y="3" width="17" height="15" rx="1.5" fill="none" stroke="#f7931e" stroke-width="2"/><rect x="1" y="3" width="17" height="4" fill="#f7931e"/><rect x="5" y="0" width="2" height="5" fill="#f7931e"/><rect x="12" y="0" width="2" height="5" fill="#f7931e"/><g fill="#f7931e"><rect x="4" y="9" width="2.5" height="2"/><rect x="8.3" y="9" width="2.5" height="2"/><rect x="12.5" y="9" width="2.5" height="2"/><rect x="4" y="13" width="2.5" height="2"/><rect x="8.3" y="13" width="2.5" height="2"/><rect x="12.5" y="13" width="2.5" height="2"/></g></svg>
    <span><small>BOOK AN</small><strong>APPOINTMENT</strong></span>
  </a>
  <div class="header-divider"></div>
  <a class="quick-link ql-tools" href="#">
    <svg width="18" height="18" viewBox="0 0 18 18"><g fill="#2fa3d6"><circle cx="9" cy="9" r="6"/><rect x="7.5" y="0" width="3" height="18" rx="1"/><rect x="0" y="7.5" width="18" height="3" rx="1"/><rect x="7.5" y="0" width="3" height="18" rx="1" transform="rotate(45 9 9)"/><rect x="7.5" y="0" width="3" height="18" rx="1" transform="rotate(-45 9 9)"/></g><circle cx="9" cy="9" r="2.5" fill="#f3f3f3"/></svg>
    <span><small>PHYSICIAN</small><strong>TOOLBOX</strong></span>
  </a>
</header>

<ul class="main-nav">
  <li class="active"><span class="dot"><svg width="11" height="10" viewBox="0 0 11 10"><path d="M5.5 0 0 5h1.5v5h3V7h2v3h3V5H11z" fill="#fff"/></svg></span>HOME</li>
  <li><span class="dot"><svg width="8" height="10" viewBox="0 0 8 10"><rect x="0.5" y="0.5" width="7" height="9" fill="none" stroke="#fff"/><rect x="3.3" y="2" width="1.4" height="4" fill="#fff"/><rect x="2" y="3.3" width="4" height="1.4" fill="#fff"/></svg></span>OUR CLINIC</li>
  <li><span class="dot"><svg width="12" height="9" viewBox="0 0 12 9"><g fill="#fff"><circle cx="6" cy="2.5" r="2.2"/><path d="M2 9c0-3 2-4.5 4-4.5S10 6 10 9z"/><circle cx="2" cy="3" r="1.4"/><circle cx="10" cy="3" r="1.4"/></g></svg></span>OUR STAFF</li>
  <li><span class="dot"><svg width="9" height="10" viewBox="0 0 9 10"><path d="M3 0h3v1H5.5v3L9 9.5H0L3.5 4V1H3z" fill="#fff"/></svg></span>RESOURCES</li>
  <li><span class="dot"><svg width="9" height="10" viewBox="0 0 9 10"><path d="M4.5 0C2.3 0 1.5 2 1.5 4v2.5L0 8h9L7.5 6.5V4C7.5 2 6.7 0 4.5 0zM3.3 8.7h2.4a1.2 1.2 0 0 1-2.4 0z" fill="#fff"/></svg></span>ALERTS</li>
  <li><span class="dot"><svg width="10" height="8" viewBox="0 0 10 8"><rect width="10" height="8" rx="1" fill="#fff"/><path d="M0.5 1 5 4.5 9.5 1" fill="none" stroke="#2b2b2b"/></svg></span>CONTACT US</li>
</ul>

<div class="content-edge"></div>

<section class="content" style="top:75px">
  <h2 class="section-title"><svg width="13" height="14" viewBox="0 0 13 14"><circle cx="6.5" cy="3.5" r="3.3" fill="#222"/><path d="M0 14c0-4 2.5-6.5 6.5-6.5S13 10 13 14z" fill="#222"/></svg>NEW PATIENTS</h2>
  <p class="lead">Accepting new patients</p>
  <a class="btn-solid" href="#">CONTACT US</a>
</section>
<div class="divider" style="top:167px"></div>

<section class="content" style="top:188px">
  <h2 class="section-title"><svg width="12" height="15" viewBox="0 0 12 15"><rect x="0.8" y="0.8" width="10.4" height="13.4" fill="none" stroke="#222" stroke-width="1.6"/><rect x="5" y="3" width="2" height="5" fill="#222"/><rect x="3.5" y="4.5" width="5" height="2" fill="#222"/><rect x="4.5" y="10" width="3" height="4" fill="#222"/></svg>ABOUT OUR CLINIC</h2>
  <p class="body-copy">Lorem Ipsum is simply dummy text of the printing and typesetting industry. Lorem Ipsum has been the industry's standard dummy text ever since the 1500s, when an unknown printer took a galley of type and scrambled it to make a type specimen book. It has survived not only five centuries, but also the leap into electronic typesetting, remaining essentially unchanged. It was popularised in the 1960s with the release of Typeset Co sheets containing Lorem Ipsum passages, and more recently with desktop publishing software like Draftwise PageSetter including versions of Lorem Ipsum.</p>
</section>
<div class="divider" style="top:380px"></div>

<section class="content" style="top:399px">
  <h2 class="section-title"><svg width="17" height="13" viewBox="0 0 17 13"><g fill="#222"><circle cx="8.5" cy="3.5" r="3"/><path d="M3.5 13c0-4 2-6 5-6s5 2 5 6z"/><circle cx="3" cy="4" r="2.2"/><circle cx="14" cy="4" r="2.2"/><path d="M0 11c0-3 1.3-4.5 3-4.5 1 0 1.5.3 1.5.3-.8 1.3-1.2 2.5-1.3 4.2z"/><path d="M17 11c0-3-1.3-4.5-3-4.5-1 0-1.5.3-1.5.3.8 1.3 1.2 2.5 1.3 4.2z"/></g></svg>OUR STAFF</h2>
  <ul class="staff-list">
    <li class="staff-row"><div class="staff-id"><b>DR. JOHN SMITH, MD</b>Physician</div><div class="staff-bio">In publishing and graphic design, lorem ipsum is a filler text a document or visual presentation... [<i>Read more</i>]</div></li>
    <li class="staff-row"><div class="staff-id"><b>DR. JANE DOE, MD</b>Therapist</div><div class="staff-bio">In publishing and graphic design, lorem ipsum is a filler text a document or visual presentation... [<i>Read more</i>]</div></li>
    <li class="staff-row"><div class="staff-id"><b>DR. WILLSON, MD</b>Radiologist</div><div class="staff-bio">In publishing and graphic design, lorem ipsum is a filler text a document or visual presentation... [<i>Read more</i>]</div></li>
    <li class="staff-row"><div class="staff-id"><b>DR. JOHN SMITH, MD</b>Physician</div><div class="staff-bio">In publishing and graphic design, lorem ipsum is a filler text a document or visual presentation... [<i>Read more</i>]</div></li>
    <li class="staff-row"><div class="staff-id"><b>DR. JOHN SMITH, MD</b>Physician</div><div class="staff-bio">In publishing and graphic design, lorem ipsum is a filler text a document or visual presentation... [<i>Read more</i>]</div></li>
  </ul>
  <a class="btn-outline" href="#" style="margin-top:12px">VIEW ALL STAFF</a>
</section>
<div class="divider" style="top:740px"></div>

<section class="content" style="top:757px">
  <h2 class="section-title"><svg width="13" height="14" viewBox="0 0 9 10"><path d="M4.5 0C2.3 0 1.5 2 1.5 4v2.5L0 8h9L7.5 6.5V4C7.5 2 6.7 0 4.5 0zM3.3 8.7h2.4a1.2 1.2 0 0 1-2.4 0z" fill="#222"/></svg>ALERTS</h2>
  <article class="alert-item" style="margin-top:11px">
    <h3>A HANDY LOREM IPSUM GENERATOR THAT HELPS TO CREATE DUMMY TEXT FOR ALL LAYOUT NEEDS</h3>
    <p>In publishing and graphic design, lorem ipsum is a filler text commonly used to demonstrate the graphic elements of a document or visual presentation.Lorem ipsum dolor sit amet, consectetuer adipiscing elit, sed diam nonummy nibh euismod tincidunt ut laoreet dolore magna aliquam erat volutpat. Ut wisi enim ...</p>
  </article>
  <article class="alert-item" style="margin-top:19px">
    <h3>A HANDY LOREM IPSUM GENERATOR THAT HELPS TO CREATE DUMMY TEXT FOR ALL LAYOUT NEEDS</h3>
    <p>In publishing and graphic design, lorem ipsum is a filler text commonly used to demonstrate the graphic elements of a document or visual presentation.Lorem ipsum dolor sit amet, consectetuer adipiscing elit, sed diam nonummy nibh euismod tincidunt ut laoreet dolore magna aliquam erat volutpat. Ut wisi enim ...</p>
  </article>
</section>
<div class="divider" style="top:971px"></div>

<section class="content" style="top:989px">
  <h2 class="section-title"><svg width="12" height="15" viewBox="0 0 12 15"><path d="M0 0h8l4 4v11H0z" fill="#222"/><path d="M8 0v4h4" fill="#fff"/></svg>CLINIC POLICIES</h2>
  <ul class="policy-list">
    <li><svg width="7" height="6" viewBox="0 0 7 6"><path d="M0 3h6M4 1l2 2-2 2" fill="none" stroke="#888" stroke-width=".8"/></svg>LATE ARRIVALS</li>
    <li><svg width="7" height="6" viewBox="0 0 7 6"><path d="M0 3h6M4 1l2 2-2 2" fill="none" stroke="#888" stroke-width=".8"/></svg>MISSED APPOINTMENTS</li>
    <li><svg width="7" height="6" viewBox="0 0 7 6"><path d="M0 3h6M4 1l2 2-2 2" fill="none" stroke="#888" stroke-width=".8"/></svg>FEES</li>
  </ul>
  <a class="btn-outline" href="#" style="margin-top:11px">VIEW ALL CLINIC POLICIES</a>
</section>

<aside class="sidebar">
  <div class="widget-head wh-hours">
    <svg width="22" height="22" viewBox="0 0 22 22"><circle cx="11" cy="11" r="9.5" fill="none" stroke="#fff" stroke-width="2"/><path d="M11 5v6h4" fill="none" stroke="#fff" stroke-width="2"/></svg>
    <div>HOURS OF<span>OPERATION</span></div>
  </div>
  <dl class="info-table" style="padding-top:10px">
    <div class="info-row" style="height:23px"><dt>MONDAY</dt><span class="sep">:</span><dd>8:00am - 6:00pm</dd></div>
    <div class="info-row" style="height:23px"><dt>TUESDAY</dt><span class="sep">:</span><dd>8:00am - 6:00pm</dd></div>
    <div class="info-row" style="height:23px"><dt>WEDNESDAY</dt><span class="sep">:</span><dd>8:00am - 6:00pm</dd></div>
    <div class="info-row" style="height:23px"><dt>THURSDAY</dt><span class="sep">:</span><dd>8:00am - 6:00pm</dd></div>
    <div class="info-row" style="height:23px"><dt>FRIDAY</dt><span class="sep">:</span><dd>8:00am - 6:00pm</dd></div>
    <div class="info-row" style="height:23px"><dt>SATURDAY</dt><span class="sep">:</span><dd>9:00am - 4:00pm</dd></div>
    <div class="info-row" style="height:23px"><dt>SUNDAY</dt><span class="sep">:</span><dd>9:00am - 4:00pm</dd></div>
  </dl>
  <div class="widget-head wh-contact" style="position:absolute;top:210px;width:135px">
    <svg width="24" height="18" viewBox="0 0 24 18"><rect width="24" height="18" rx="2" fill="#fff"/><path d="M1 2l11 8 11-8" fill="none" stroke="#f7931e" stroke-width="2"/></svg>
    <div>CONTACT<span>INFORMATION</span></div>
  </div>
  <dl class="info-table" style="position:absolute;top:258px;width:135px">
    <div class="info-row" style="height:21px"><dt>TELEPHONE</dt><span class="sep">:</span><dd>604 555 0142</dd></div>
    <div class="info-row" style="height:22px"><dt>FAX</dt><span class="sep">:</span><dd>604 555 0143</dd></div>
    <div class="info-row" style="height:21px"><dt>EMAIL</dt><span class="sep">:</span><dd class="link">info@hsclinic.ca</dd></div>
    <div class="info-row" style="height:44px"><dt>ADDRESS</dt><span class="sep">:</span><dd>48 Cedar Lane, Kelvale, B.C, Canada, V0X2Y9</dd></div>
    <div class="info-row"><dt>DIRECTIONS</dt><span class="sep">:</span><dd class="link">Atlas Maps</dd></div>
  </dl>
</aside>

<div class="footer-rule"></div>
<footer class="site-footer">
  <p>©2015 Harbourside Clinic. All Rights Reserved</p>
  <p>Terms &amp; Privacy Policy | Sitemap</p>
</footer>

</body>
</html>
```